RB Halden Electric Yard Sign

Looking to have a yard sign designed that we can place at projects we are working on. Most likely will be 18" H x 24" W but flexible that we can increase the size if necessary. It should include our logo, our phone # 609-555-0147, website rbhaldenelectric.example and slogan, built on integrity, driven by excellence. Colors should match our brand.

```html
<!DOCTYPE html>
<html lang="en">
<head>
<meta charset="utf-8">
<title>RB Halden Electric Yard Sign</title>
<link rel="stylesheet" href="https://fonts.googleapis.com/css2?family=Poppins:wght@400;600;700;800&display=swap">
<style>
  :root {
    --sign-white: #ffffff;
    --brand-red: #ec2227;
    --brand-navy: #1a345f;
    --ink-navy: #1b2f55;
  }
  * { margin: 0; padding: 0; box-sizing: border-box; }
  html, body {
    width: 1200px;
    height: 877px;
    overflow: hidden;
    background: var(--sign-white);
  }
  .yard-sign {
    position: relative;
    width: 1200px;
    height: 877px;
    background: var(--sign-white);
    font-family: "Poppins", sans-serif;
  }
  .brand-lockup {
    position: absolute;
    top: 180px;
    left: 0;
    width: 100%;
    display: flex;
    align-items: center;
    justify-content: center;
    gap: 28px;
  }
  .brand-dot {
    width: 64px;
    height: 64px;
    border-radius: 50%;
    background: var(--brand-navy);
    flex: none;
  }
  .brand-name {
    font-weight: 700;
    font-size: 92px;
    line-height: 1;
    letter-spacing: 3px;
    text-transform: uppercase;
    color: var(--brand-red);
  }
  .contact-band {
    position: absolute;
    left: 18px;
    right: 17px;
    top: 437px;
    border-top: 12px solid var(--brand-navy);
  }
  .phone-panel {
    height: 196px;
    background: var(--brand-red);
    display: flex;
    align-items: center;
    justify-content: center;
  }
  .phone-number {
    font-weight: 700;
    font-size: 128px;
    line-height: 1;
    color: var(--sign-white);
    letter-spacing: 1px;
  }
  .slogan-panel {
    height: 103px;
    background: var(--brand-navy);
    display: flex;
    align-items: center;
    justify-content: center;
  }
  .slogan {
    font-weight: 700;
    font-size: 39px;
    color: var(--sign-white);
  }
  .website {
    position: absolute;
    top: 762px;
    left: 0;
    width: 100%;
    text-align: center;
    font-weight: 400;
    font-size: 46px;
    letter-spacing: 0.5px;
    color: var(--ink-navy);
  }
</style>
</head>
<body>
  <main class="yard-sign">
    <header class="brand-lockup">
      <span class="brand-dot" aria-hidden="true"></span>
      <h1 class="brand-name">R.B. Halden</h1>
    </header>
    <section class="contact-band">
      <div class="phone-panel">
        <p class="phone-number">609-555-0147</p>
      </div>
      <div class="slogan-panel">
        <p class="slogan">Built on Integrity, Driven by Excellence.</p>
      </div>
    </section>
    <p class="website">www.rbhaldenelectric.example</p>
  </main>
</body>
</html>
```